Corvane Capital Business Cards

These are professional business cards that are for my family office.
Put fake emails and phone numbers as of now until I finalize those components. This family office controls my families investments, assets, and future. The cards should be professional.
..
.
.
.
I just uploaded another variation of a logo I would like to see as a business card to I am inbeteen which logo to use

Target Market(s)

business

Industry/Entity Type

business

Contact Information for Business Card

Professional, wealth related, finance related.

Requirements
Must have
• Logo

```html
<!DOCTYPE html>
<html lang="en">
<head>
<meta charset="utf-8">
<title>Corvane Capital Business Cards</title>
<link href="https://fonts.googleapis.com/css2?family=Cinzel:wght@400;600&family=Tinos:wght@400;700&display=swap" rel="stylesheet">
<style>
  :root {
    --stage: #b9b9b9;
    --card-black: #050505;
    --ink-white: #ffffff;
    --band-grey: #b3b3b3;
    --pattern-dark: #0c0c0c;
    --pattern-mid: #2a2a2a;
  }
  * { margin: 0; padding: 0; box-sizing: border-box; }
  html, body { width: 1200px; height: 721px; overflow: hidden; }
  body {
    background: radial-gradient(ellipse at 55% 30%, #d2d2d2 0%, var(--stage) 60%, #9c9c9c 100%);
    position: relative;
    font-family: "Tinos", "Times New Roman", serif;
    color: var(--ink-white);
  }
  .card {
    position: absolute;
    top: 212px;
    width: 520px;
    height: 297px;
    background: var(--card-black);
    border-radius: 12px;
    overflow: hidden;
    box-shadow: 0 14px 30px rgba(0,0,0,0.35);
  }
  .card--back { left: 60px; }
  .card--front { left: 620px; }

  .back-pattern {
    position: absolute;
    inset: 0;
    background: linear-gradient(100deg, var(--pattern-mid) 0%, #1a1a1a 35%, var(--pattern-dark) 75%, #161616 100%);
  }
  .wordmark {
    font-family: "Cinzel", "Times New Roman", serif;
    font-weight: 400;
    color: var(--ink-white);
    white-space: nowrap;
    letter-spacing: 0.5px;
  }
  .card--back .wordmark {
    position: absolute;
    right: 34px;
    top: 138px;
    font-size: 21px;
  }

  .card--front .wordmark {
    position: absolute;
    left: 30px;
    top: 70px;
    font-size: 22px;
  }
  .person {
    position: absolute;
    left: 74px;
    top: 118px;
  }
  .person__name { font-size: 19px; font-weight: 700; line-height: 1.1; }
  .person__role { font-size: 13px; margin-top: 2px; }
  .person__rule {
    display: block;
    width: 16px;
    height: 3px;
    background: var(--ink-white);
    margin-top: 9px;
  }
  .contact {
    position: absolute;
    left: 80px;
    top: 178px;
    list-style: none;
    font-size: 14px;
    line-height: 20px;
  }
  .contact li { display: flex; align-items: center; gap: 6px; }
  .contact svg { width: 12px; height: 12px; flex: none; }

  .band {
    position: absolute;
    left: 0; top: 0;
    width: 520px; height: 297px;
  }
</style>
</head>
<body>

  <section class="card card--back" aria-label="Card back">
    <div class="back-pattern" role="img" aria-label="Repeating monogram emblem pattern in white and grey on black"></div>
    <p class="wordmark">Corvane Capital</p>
  </section>

  <section class="card card--front" aria-label="Card front">
    <svg class="band" viewBox="0 0 520 297" aria-hidden="true">
      <rect x="420" y="222" width="100" height="34" fill="var(--band-grey)"/>
      <rect x="0" y="238" width="420" height="32" fill="var(--ink-white)"/>
      <circle cx="420" cy="240" r="25" fill="var(--card-black)" stroke="var(--ink-white)" stroke-width="2"/>
    </svg>

    <p class="wordmark">Corvane Capital</p>

    <div class="person">
      <p class="person__name">Daniel Hart</p>
      <p class="person__role">Founder</p>
      <span class="person__rule"></span>
    </div>

    <ul class="contact">
      <li>
        <svg viewBox="0 0 12 12" aria-hidden="true"><path d="M1 4c0-2 2-3 5-3s5 1 5 3v1H8.5V3.8C8 3.3 7 3 6 3s-2 .3-2.5.8V5H1z M2.5 6h7l1 5h-9z" fill="#fff"/><circle cx="6" cy="8.4" r="1.3" fill="#050505"/></svg>
        <span>555-210-4417</span>
      </li>
      <li>
        <svg viewBox="0 0 12 12" aria-hidden="true"><rect x="0.5" y="2.5" width="11" height="7" fill="#fff"/><path d="M0.8 2.8L6 6.8l5.2-4" stroke="#050505" stroke-width="1" fill="none"/></svg>
        <span>info@corvanecapital.com</span>
      </li>
    </ul>
  </section>

</body>
</html>
```